Business Card Design and Logo Needed

I need Business Cards and a Logo for my website and public speaking business which can be found at: www.corvina-lett.example

I'm looking for creative and unique ideas. Some business cards I've found online that I like can be found at:
http://gigbarrow.example/general/18-smokin-hot-business-card-designs/

and at

http://www.plumquarry.example/2009/04/50-creative-business-cards-of-50-graphic-designers/

```html
<!DOCTYPE html>
<html lang="en">
<head>
<meta charset="utf-8">
<title>Corvina Lett – Card</title>
<link rel="stylesheet" href="https://fonts.googleapis.com/css2?family=Parisienne&display=swap">
<style>
  :root {
    --page: #ffffff;
    --banner: #fdd49a;
    --disc-light: #fee2a6;
    --disc-deep: #ff8550;
    --name: #f2785a;
  }
  html, body {
    margin: 0;
    padding: 0;
    width: 1062px;
    height: 1200px;
    overflow: hidden;
    background: var(--page);
  }
  .card {
    position: relative;
    width: 1062px;
    height: 1200px;
  }
  .banner {
    position: absolute;
    left: 0;
    top: 0;
    width: 1062px;
    height: 1200px;
  }
  .brand-name {
    position: absolute;
    left: 224px;
    width: 662px;
    top: 815px;
    margin: 0;
    text-align: center;
    font-family: "Parisienne", cursive;
    font-weight: 400;
    font-size: 108px;
    line-height: 1;
    white-space: nowrap;
    color: var(--name);
  }
</style>
</head>
<body>
  <main class="card">
    <svg class="banner" viewBox="0 0 1062 1200" aria-hidden="true">
      <defs>
        <linearGradient id="disc-fill" x1="0" y1="0" x2="0" y2="1">
          <stop offset="0" stop-color="var(--disc-light)"/>
          <stop offset="1" stop-color="var(--disc-deep)"/>
        </linearGradient>
      </defs>
      <path class="banner-shape" d="M224 47 H886 V1020 Q555 1195 224 1020 Z" fill="var(--banner)"/>
      <circle class="brand-disc" cx="555" cy="525" r="200" fill="url(#disc-fill)"/>
    </svg>
    <h1 class="brand-name">Corvina Lett</h1>
  </main>
</body>
</html>
```